Business Card Design Project

i need a bussines car design
Velora Clinical Hypnotherapy

Daniel Wexford
Psychotherapy & Hypnosis

84261937 /0427591628

back of the card appoinment space.

file was provided on a PDF, LOgo , use the blu colorsa as well , elegant, clear,

Target Market(s)

young professional, caucasian , young mothers.

Industry/Entity Type

Business

```html
<!DOCTYPE html>
<html lang="en">
<head>
<meta charset="utf-8">
<title>Velora Clinical Hypnotherapy – Business Card</title>
<link rel="stylesheet" href="https://fonts.googleapis.com/css2?family=Open+Sans:wght@400;600;700&display=swap">
<style>
  :root {
    --bg: #e4e4e4;
    --card: #f7f7f6;
    --ink: #3a3a3a;
    --ink-soft: #6a6a6a;
    --blue: #3d7fc0;
    --blue-deep: #2f6fae;
    --blue-light: #a9c8e6;
    --rule: #6b9fd2;
  }
  * { box-sizing: border-box; margin: 0; padding: 0; }
  html, body { width: 1200px; height: 747px; overflow: hidden; }
  body {
    background: var(--bg);
    font-family: "Open Sans", Arial, sans-serif;
    color: var(--ink);
    display: flex;
    justify-content: center;
    align-items: center;
    gap: 60px;
  }
  .card {
    width: 340px;
    height: 620px;
    background: var(--card);
    box-shadow: 0 2px 6px rgba(0,0,0,0.12);
    position: relative;
    overflow: hidden;
    padding: 26px 24px;
  }
  .brand { text-align: center; }
  .brand-name {
    font-size: 27px;
    font-weight: 400;
    color: var(--blue);
    letter-spacing: 0.5px;
    line-height: 1.1;
  }
  .brand-web {
    font-size: 10.5px;
    letter-spacing: 1px;
    color: var(--ink-soft);
    margin-top: 4px;
    padding-bottom: 5px;
    border-bottom: 1.5px solid var(--rule);
  }
  /* back */
  .contact {
    text-align: center;
    font-size: 11px;
    line-height: 1.75;
    margin-top: 14px;
    color: var(--ink);
  }
  .contact .lead { font-weight: 600; }
  .appointments { margin-top: 56px; padding: 0 8px; }
  .appointments h2 {
    text-align: center;
    font-size: 15px;
    font-weight: 700;
    margin-bottom: 16px;
  }
  .slot {
    display: flex;
    align-items: flex-end;
    gap: 4px;
    font-size: 13px;
    color: var(--ink-soft);
    height: 34px;
  }
  .slot .blank { border-bottom: 1px solid var(--ink-soft); height: 14px; }
  .slot .time { width: 24px; }
  .slot .place { flex: 1; }
  .slot .d { width: 20px; }
  .note {
    margin-top: 40px;
    font-size: 9px;
    line-height: 1.6;
    color: var(--ink-soft);
  }
  .reg {
    margin-top: 16px;
    font-size: 10.5px;
    font-weight: 600;
    color: var(--ink-soft);
  }
  /* front */
  .motif {
    display: block;
    margin: 26px -24px 0;
    width: 340px;
    height: 170px;
  }
  .person { text-align: center; margin-top: 56px; }
  .person-name {
    font-size: 23px;
    font-weight: 700;
    letter-spacing: 0.6px;
    color: var(--ink);
  }
  .person-role { font-size: 13px; color: var(--ink-soft); margin-top: 2px; }
  .phones { margin: 58px 0 0 40px; }
  .phone {
    display: flex;
    align-items: center;
    gap: 10px;
    font-size: 19px;
    letter-spacing: 0.5px;
    margin-bottom: 12px;
  }
  .phone svg { width: 18px; height: 20px; fill: var(--blue); }
  .address {
    position: absolute;
    bottom: 22px;
    left: 0;
    right: 0;
    text-align: center;
    font-size: 13px;
    color: var(--ink);
  }
</style>
</head>
<body>

<section class="card card-back">
  <header class="brand">
    <div class="brand-name">Velora Hypnotherapy</div>
    <div class="brand-web">www.veloraclinicalhypnotherapy.com.au</div>
  </header>
  <div class="contact">
    <div class="lead">By Appointment · Phone: 0427 591 628</div>
    <div>48 Kestrel Lane, Brookvale 3124</div>
    <div>hello@veloraclinicalhypnotherapy.com.au</div>
  </div>
  <div class="appointments">
    <h2>Your Appointments</h2>
    <div class="slot">1. <span class="blank time"></span>am/pm <span class="blank place"></span> <span class="blank d"></span>/<span class="blank d"></span>/<span class="blank d"></span></div>
    <div class="slot">2. <span class="blank time"></span>am/pm <span class="blank place"></span> <span class="blank d"></span>/<span class="blank d"></span>/<span class="blank d"></span></div>
    <div class="slot">3. <span class="blank time"></span>am/pm <span class="blank place"></span> <span class="blank d"></span>/<span class="blank d"></span>/<span class="blank d"></span></div>
    <div class="slot">4. <span class="blank time"></span>am/pm <span class="blank place"></span> <span class="blank d"></span>/<span class="blank d"></span>/<span class="blank d"></span></div>
    <div class="slot">5. <span class="blank time"></span>am/pm <span class="blank place"></span> <span class="blank d"></span>/<span class="blank d"></span>/<span class="blank d"></span></div>
    <p class="note">To reschedule your appointment, please SMS or phone 0427 591 628 at least 24 hours prior to your allocated time. Thank you.</p>
    <p class="reg">NMRA Registration No. NPM048215</p>
  </div>
</section>

<section class="card card-front">
  <header class="brand">
    <div class="brand-name">Velora Hypnotherapy</div>
    <div class="brand-web">www.veloraclinicalhypnotherapy.com.au</div>
  </header>
  <svg class="motif" role="img" aria-label="Swinging pendulum brand illustration in shades of blue" viewBox="0 0 340 170" preserveAspectRatio="none">
    <defs>
      <linearGradient id="motifFill" x1="0" y1="0" x2="1" y2="0">
        <stop offset="0" stop-color="#a9c8e6" stop-opacity="0.5"/>
        <stop offset="0.5" stop-color="#3d7fc0"/>
        <stop offset="1" stop-color="#a9c8e6" stop-opacity="0.5"/>
      </linearGradient>
    </defs>
    <rect x="0" y="0" width="340" height="170" fill="url(#motifFill)" opacity="0.55"/>
  </svg>
  <div class="person">
    <div class="person-name">DANIEL WEXFORD</div>
    <div class="person-role">Psychotherapy &amp; Hypnosis</div>
  </div>
  <div class="phones">
    <div class="phone">
      <svg viewBox="0 0 18 20" aria-hidden="true"><path d="M5 1h8a2 2 0 0 1 2 2v14a2 2 0 0 1-2 2H5a2 2 0 0 1-2-2V3a2 2 0 0 1 2-2zm0 3v10h8V4zm4 11.5a1 1 0 1 0 0 2 1 1 0 0 0 0-2z"/></svg>
      <span>8426 1937</span>
    </div>
    <div class="phone">
      <svg viewBox="0 0 18 20" aria-hidden="true"><path d="M1 5h3v13H1zM5 3h12v15H5zm2 2v3h8V5zm0 5v2h2v-2zm3 0v2h2v-2zm3 0v2h2v-2zm-6 3v2h2v-2zm3 0v2h2v-2zm3 0v2h2v-2z"/></svg>
      <span>0427 591 628</span>
    </div>
  </div>
  <div class="address">112 Harlow Road, Brookvale</div>
</section>

</body>
</html>
```